Naturopath Practitioner Card Design

I am a naturopath needing a design for a business card mainly to show that I am a naturopath and have some contact details to give to prospective clients. I am open minded about the design and what is on the second side of the card whether it just be some artwork or space for details, appointment times etc. Naturopathy is the practice of natural medicine that uses a holistic approach and incorporates herbal and nutritional medicine.

Industry/Entity Type

Business

Contact Information for Business Card

Tom Rudd NaturopathBHSc (Naturopathy) Member WHPG 0487 925 316 tom.rudd@mailexample.com www.tomruddnaturopathy.example.au

Requirements
Nice to have
• Would prefer some kind of original pattern/art work/logo rather than an image, not fussed if its very simple/basic
• I am open to any colour but think I would prefer a more earthy sandy clay etc type style than the greens that are commonly associated with naturopathy.
Should not have
• Don't really want to have generic stock images on it

```html
<!DOCTYPE html>
<html lang="en">
<head>
<meta charset="utf-8">
<title>Tom Rudd Naturopath – Business Card</title>
<link href="https://fonts.googleapis.com/css2?family=Cinzel:wght@400&family=Source+Sans+3:ital,wght@0,400;0,600;1,600&display=swap" rel="stylesheet">
<style>
  :root {
    --backdrop-top: #262626;
    --backdrop-bottom: #050505;
    --green-light: #79dd16;
    --green-mid: #35a818;
    --green-deep: #0a6a12;
    --leaf-dark: #2f8a22;
    --leaf-light: #8fd05a;
    --ink-white: #ffffff;
    --ink-green: #5aa92a;
    --ink-label: #3f6d2c;
    --rule: #b9df9c;
  }
  * { margin: 0; padding: 0; box-sizing: border-box; }
  html, body { width: 1200px; height: 900px; overflow: hidden; }
  body {
    background: linear-gradient(180deg, var(--backdrop-top) 0%, #1a1a1a 55%, var(--backdrop-bottom) 100%);
    font-family: "Source Sans 3", "Myriad Pro", sans-serif;
    position: relative;
  }
  .card {
    position: absolute;
    top: 306px;
    width: 440px;
    height: 271px;
    border-radius: 10px;
    overflow: hidden;
  }
  .card--front {
    left: 149px;
    background: radial-gradient(ellipse 70% 55% at 50% 25%, var(--green-light) 0%, var(--green-mid) 55%, transparent 100%),
                linear-gradient(180deg, #4cbf18 0%, #2e9a16 55%, var(--green-deep) 100%);
    color: var(--ink-white);
  }
  .card--back { left: 608px; background: #fff; }
  .foliage { position: absolute; inset: 0; width: 100%; height: 100%; }
  .text { position: absolute; left: 0; width: 100%; text-align: center; }
  .practitioner-name {
    top: 80px; font-family: "Cinzel", serif; font-size: 26px; letter-spacing: 0.5px;
  }
  .role { top: 114px; font-size: 12.5px; line-height: 17px; }
  .contact { top: 199px; font-size: 16px; line-height: 21px; }
  .contact-line { display: flex; align-items: center; justify-content: center; gap: 7px; }
  .contact-line svg { flex: none; }
  .appointment-title {
    top: 68px; font-size: 19px; font-weight: 600; color: var(--ink-green);
  }
  .field { position: absolute; font-size: 13px; color: var(--ink-label); }
  .rule { position: absolute; height: 1px; background: var(--rule); }
  .notice {
    top: 213px; font-size: 12.5px; font-style: italic; font-weight: 600; color: var(--ink-green);
  }
</style>
</head>
<body>

<section class="card card--front" aria-label="Business card front">
  <svg class="foliage" viewBox="0 0 440 271" role="img" aria-label="Border of green leaves framing the card">
    <defs>
      <linearGradient id="leafFront" x1="0" y1="0" x2="0" y2="1">
        <stop offset="0" stop-color="#5cc22e"/>
        <stop offset="1" stop-color="#1f7a1a"/>
      </linearGradient>
    </defs>
    <path d="M0 0 H440 V271 H420 C395 230 405 190 385 160 C370 120 400 90 360 60 C330 40 300 45 270 20 C240 35 200 25 170 20 C140 40 110 35 80 50 C60 80 55 120 40 160 C35 200 25 240 15 271 H0 Z" fill="url(#leafFront)" opacity="0.75"/>
  </svg>
  <div class="text practitioner-name">Tom Rudd</div>
  <div class="text role">Naturopath<br>BHSc (Naturopathy) Member WHPG</div>
  <div class="text contact">
    <div class="contact-line">
      <svg width="12" height="12" viewBox="0 0 24 24" aria-hidden="true"><path fill="#fff" d="M6.6 10.8a15 15 0 0 0 6.6 6.6l2.2-2.2a1 1 0 0 1 1-.25 11.4 11.4 0 0 0 3.6.57 1 1 0 0 1 1 1V20a1 1 0 0 1-1 1A17 17 0 0 1 3 4a1 1 0 0 1 1-1h3.5a1 1 0 0 1 1 1c0 1.25.2 2.45.57 3.57a1 1 0 0 1-.25 1z"/></svg>
      <span>0487 925 316</span>
    </div>
    <div class="contact-line">
      <svg width="11" height="9" viewBox="0 0 22 16" aria-hidden="true"><rect width="22" height="16" rx="1.5" fill="#fff"/><path d="M1 1.5 11 9 21 1.5" stroke="#2e8a16" stroke-width="1.6" fill="none"/></svg>
      <span>tom.rudd@mailexample.com</span>
    </div>
  </div>
</section>

<section class="card card--back" aria-label="Business card back: appointment card">
  <svg class="foliage" viewBox="0 0 441 271" role="img" aria-label="Border of green leaves across the top and down both sides">
    <defs>
      <linearGradient id="leafBack" x1="0" y1="0" x2="0" y2="1">
        <stop offset="0" stop-color="#4fae2c"/>
        <stop offset="1" stop-color="#8fd05a"/>
      </linearGradient>
    </defs>
    <path d="M0 0 H441 V271 H425 C430 230 405 200 395 170 C385 140 390 110 370 80 C350 55 330 40 300 30 C270 45 240 35 215 40 C190 30 160 45 130 35 C100 40 75 30 55 40 C35 60 25 100 20 140 C12 180 8 230 12 271 H0 Z" fill="url(#leafBack)" opacity="0.8"/>
  </svg>
  <div class="text appointment-title">Your Next Appointment is</div>

  <span class="field" style="left:64px; top:114px;">Name :</span>
  <span class="rule" style="left:111px; top:125px; width:253px;"></span>

  <span class="field" style="left:64px; top:146px;">Date :</span>
  <span class="rule" style="left:111px; top:155px; width:255px;"></span>

  <span class="field" style="left:66px; top:172px;">Time:</span>
  <span class="rule" style="left:112px; top:183px; width:85px;"></span>
  <span class="field" style="left:203px; top:172px;">AM</span>
  <span class="rule" style="left:232px; top:183px; width:120px;"></span>
  <span class="field" style="left:359px; top:172px;">PM</span>

  <div class="text notice">If unable to keep appointment, kindly give 24hrs notice.</div>
</section>

</body>
</html>
```